Tobias Ränkel and Co stationary design

Name of business:
Tobias Ränkel and Co

Can be written as:
Tobias Ränkel and Co
Tobias Ränkel & Co
tobias ränkel & co

If broken into letters:
TR&Co
tr&co

We are a Railway Safety Training Company
Our focus is on rail safety, Rail Management, Safety Management, Train Control Training, Accident Investigation.

.

Project Deadline Extended Reason: The original date was set to commence as soon as the logo contest finished. Sketch harbor started the project as soon as it was paid. Added Thursday, May 12, 2016

Target Market(s)

Professionals, CEO's and Managing Directors

Industry/Entity Type

Management Consulting

Font styles to use
Sans Serif

Requirements
Must have
• Professional, Sharp, Creative and modern
• Please note that this is for stationary concept which must include
• - business card
• - letterhead
• - envelope
• - with compliments slip
• - document cover (like book or folder cover)
• - dividers for folders....
• These must all have a common theme or style
Nice to have
• Keep if fresh
Should not have
• Please don't sent just fonts.... Must be creative

```html
<!DOCTYPE html>
<html lang="en">
<head>
<meta charset="utf-8">
<title>Tobias Ränkel &amp; Co — Stationery</title>
<link href="https://fonts.googleapis.com/css2?family=Exo+2:wght@600&family=Open+Sans:wght@400;600&family=Great+Vibes&display=swap" rel="stylesheet">
<style>
  :root {
    --navy: #2b3c6b;
    --red: #b51c35;
    --paper: #f7f7f7;
    --backdrop: #ececec;
    --ink: #555b66;
    --rule: #8a8f99;
  }
  * { margin: 0; padding: 0; box-sizing: border-box; }
  html, body { width: 1200px; height: 802px; overflow: hidden; }
  body { background: var(--backdrop); position: relative; font-family: "Open Sans", sans-serif; color: var(--ink); }
  .piece { position: absolute; background: var(--paper); overflow: hidden; }
  .brand { font-family: "Exo 2", sans-serif; font-weight: 600; color: var(--navy); white-space: nowrap; display: flex; align-items: center; gap: 4px; }
  .brand .dot { display: inline-block; border-radius: 50%; background: var(--red); }
  .brand.light { color: #fff; }
  .small { font-size: 5px; line-height: 7.5px; color: var(--ink); }

  /* Letterhead */
  .letterhead { left: 185px; top: 100px; width: 296px; height: 418px; }
  .letterhead .brand { position: absolute; left: 18px; top: 50px; font-size: 7.5px; }
  .letterhead .brand .dot { width: 6px; height: 6px; }
  .letterhead .footer-rule { position: absolute; left: 16px; right: 18px; top: 385px; border-top: 0.6px solid var(--rule); }
  .letterhead .contacts { position: absolute; left: 16px; top: 377px; }
  .letterhead .address { position: absolute; right: 18px; top: 388px; text-align: right; }
  .letterhead .web { letter-spacing: 1.2px; }

  /* Folder cover: plain colour bands */
  .folder { left: 532px; top: 80px; width: 349px; height: 442px; background: var(--paper); }
  .folder .band-top { position: absolute; left: 0; right: 0; top: 0; height: 118px; background: var(--red); }
  .folder .band-bottom { position: absolute; left: 0; right: 0; bottom: 0; height: 150px; background: var(--navy); }
  .folder .brand { position: absolute; left: 0; right: 0; top: 178px; justify-content: center; font-size: 17px; gap: 8px; }
  .folder .brand .dot { width: 12px; height: 12px; }

  /* Business cards */
  .card { width: 133px; height: 76px; left: 939px; }
  .card-front { top: 339px; }
  .card-front .brand { position: absolute; left: 12px; top: 34px; font-size: 6px; gap: 3px; }
  .card-front .brand .dot { width: 5px; height: 5px; }
  .card-front .details { position: absolute; left: 77px; top: 16px; font-size: 3.6px; line-height: 5.4px; }
  .card-front .person { font-size: 5px; font-weight: 600; color: var(--navy); line-height: 6px; }
  .card-front .role { color: var(--red); font-size: 3.8px; }
  .card-back { top: 437px; background: var(--navy); }
  .card-back .brand { position: absolute; left: 0; right: 0; top: 33px; justify-content: center; font-size: 6.5px; gap: 3px; }
  .card-back .brand .dot { width: 5px; height: 5px; }

  /* Envelopes and slip */
  .envelope-front { left: 86px; top: 567px; width: 330px; height: 158px; }
  .envelope-front .brand, .slip .brand { position: absolute; left: 14px; top: 45px; font-size: 7.5px; }
  .envelope-front .brand .dot, .slip .brand .dot { width: 6px; height: 6px; }
  .envelope-front .address { position: absolute; left: 12px; top: 135px; }

  .envelope-back { left: 449px; top: 567px; width: 331px; height: 158px; }
  .envelope-back svg { position: absolute; left: 0; top: 0; }
  .envelope-back .brand { position: absolute; left: 0; right: 0; top: 22px; justify-content: center; font-size: 7.5px; gap: 3px; }
  .envelope-back .brand .dot { width: 6px; height: 6px; }
  .envelope-back .web { position: absolute; left: 0; right: 0; top: 40px; text-align: center; font-size: 4.4px; color: #dfe3ee; }

  .slip { left: 811px; top: 567px; width: 330px; height: 158px; }
  .slip .lines { position: absolute; left: 12px; top: 127px; font-size: 4.6px; line-height: 11px; }
  .slip .lines b { color: var(--navy); font-weight: 600; }
  .slip .rule { position: absolute; left: 12px; right: 16px; top: 138px; border-top: 0.6px solid var(--rule); }
  .slip .compliments { position: absolute; right: 16px; top: 112px; font-family: "Great Vibes", cursive; font-size: 19px; line-height: 22px; color: var(--navy); }
</style>
</head>
<body>

<section class="piece letterhead" aria-label="Letterhead">
  <div class="brand"><span class="dot"></span>Tobias Ränkel &amp; Co</div>
  <div class="footer-rule"></div>
  <div class="contacts small">
    <div>☎ 614 552 3091</div>
    <div>▯ 723 419 8806</div>
    <div>⎙ 507 231 6648</div>
    <div>✉ info@rankelco.com</div>
  </div>
  <div class="address small">
    <div>4120 Birchwood Road</div>
    <div>Fairbanks, Alaska 34512</div>
    <div class="web">www.rankelco.com</div>
  </div>
</section>

<section class="piece folder" aria-label="Document cover">
  <div class="band-top"></div>
  <div class="band-bottom"></div>
  <div class="brand"><span class="dot"></span>Tobias Ränkel &amp; Co</div>
</section>

<section class="piece card card-front" aria-label="Business card front">
  <div class="brand"><span class="dot"></span>Tobias Ränkel &amp; Co</div>
  <div class="details">
    <div class="person">Lena Hartwig</div>
    <div class="role">CEO/Founder</div>
    <div>4120 Birchwood Road</div>
    <div>Fairbanks, Alaska 34512</div>
    <div>☎ 614 552 3091</div>
    <div>▯ 723 419 8806</div>
    <div>⎙ 507 231 6648</div>
    <div>✉ info@rankelco.com</div>
    <div>◍ www.rankelco.com</div>
  </div>
</section>

<section class="piece card card-back" aria-label="Business card back">
  <div class="brand light"><span class="dot"></span>Tobias Ränkel &amp; Co</div>
</section>

<section class="piece envelope-front" aria-label="Envelope front">
  <div class="brand"><span class="dot"></span>Tobias Ränkel &amp; Co</div>
  <div class="address small">
    <div>4120 Birchwood Road</div>
    <div>Fairbanks, Alaska 34512</div>
  </div>
</section>

<section class="piece envelope-back" aria-label="Envelope back">
  <svg width="331" height="70" viewBox="0 0 331 70">
    <path d="M0 0 H331 L325 56 Q324 62 318 62 H13 Q7 62 6 56 Z" fill="var(--navy)"/>
  </svg>
  <div class="brand light"><span class="dot"></span>Tobias Ränkel &amp; Co</div>
  <div class="web">www.rankelco.com</div>
</section>

<section class="piece slip" aria-label="With compliments slip">
  <div class="brand"><span class="dot"></span>Tobias Ränkel &amp; Co</div>
  <div class="compliments">With Compliments</div>
  <div class="rule"></div>
  <div class="lines">
    <div>4120 Birchwood Road, Fairbanks, Alaska 34512 &nbsp;<b>P :</b> 614 552 3091</div>
    <div><b>C :</b> 723 419 8806 &nbsp;<b>F :</b> 507 231 6648 &nbsp;<b>E :</b> info@rankelco.com &nbsp;<b>W :</b> www.rankelco.com</div>
  </div>
</section>

</body>
</html>
```